13 Varno - new website design project

Our company Varno Electrical is developing a new lead generation website focused on Electrical, LED Lighting and Solar Power. We need a high converting website.

Example of our current website is www.varnoelectrical-example.com.au You can take content from this website for this new design. Our colours are red, black and white. For our new website we would like to promote Varno, Spark Every Day. Please listen to the jingle.

The below link is the company jingle that we have developed.
http://www.tunecraftdemo.com.au/vrn-tc-v1/

The key for this brief is to generate leads for Electrical, LED Lighting (for commercial) and Solar Power & Storage.

Target Market(s)

Business owners in Melbourne Victoria

Number of Pages Required

4 page

Colors
ec1f27
ffffff

Requirements
Must have
• This page must be clean, be in line with company branding and a high converting lead website.

```html
<!DOCTYPE html>
<html lang="en">
<head>
<meta charset="utf-8">
<title>Varno Electrical – Why Choose Us</title>
<link rel="stylesheet" href="https://fonts.googleapis.com/css2?family=Fira+Sans:wght@500;600&family=Source+Sans+3:wght@300&display=swap">
<style>
  :root {
    --brand-red: #ec1f27;
    --white: #ffffff;
    --ink-soft: #7a7a7a;
    --top-bar: #1e1f24;
    --photo-light: #9aa6b8;
    --photo-mid: #5c6c86;
    --photo-dark: #2b3a55;
  }
  * { box-sizing: border-box; margin: 0; padding: 0; }
  html, body { width: 805px; height: 1200px; overflow: hidden; background: var(--white); }
  .page { position: relative; width: 805px; height: 1200px; overflow: hidden; background: var(--white); }
  .top-bar { position: absolute; left: 0; top: 0; width: 805px; height: 8px; background: var(--top-bar); }
  .hero { position: absolute; left: 0; top: 8px; width: 805px; height: 472px; }
  .hero-title {
    position: absolute; left: 0; top: 332px; width: 805px; text-align: center;
    font-family: "Fira Sans", sans-serif; font-weight: 600; font-size: 22px;
    color: var(--white); letter-spacing: 0.2px;
    text-shadow: 0 1px 3px rgba(0,0,0,0.35);
  }
  .feature { position: absolute; text-align: center; }
  .feature-icon { display: block; margin: 0 auto; }
  .feature-title {
    font-family: "Fira Sans", sans-serif; font-weight: 500; font-size: 20.5px;
    line-height: 25.5px; color: var(--brand-red);
  }
  .feature-text {
    font-family: "Source Sans 3", sans-serif; font-weight: 300; font-size: 11.6px;
    line-height: 15px; color: var(--ink-soft); margin: 0 auto;
  }
  .icon-line { fill: none; stroke: var(--brand-red); stroke-width: 1.3; stroke-linejoin: miter; }
</style>
</head>
<body>
<div class="page">
  <div class="top-bar"></div>

  <svg class="hero" viewBox="0 0 805 472" role="img" aria-label="Photo of a glowing energy-saving bulb standing among unlit light bulbs">
    <defs>
      <radialGradient id="heroGlow" cx="0.66" cy="0.3" r="0.8">
        <stop offset="0" stop-color="var(--photo-light)"/>
        <stop offset="0.45" stop-color="var(--photo-mid)"/>
        <stop offset="1" stop-color="var(--photo-dark)"/>
      </radialGradient>
    </defs>
    <polygon points="0,0 805,0 805,340 0,472" fill="url(#heroGlow)"/>
  </svg>
  <h1 class="hero-title">WHY SHOULD YOU CHOOSE US</h1>

  <!-- Row one -->
  <section class="feature" style="left:53px; top:532px; width:230px;">
    <svg class="feature-icon" width="150" height="90" viewBox="0 0 150 90">
      <polygon class="icon-line" points="75,3 85,31 115,32 91,50 100,79 75,62 50,79 59,50 35,32 65,31"/>
      <polygon class="icon-line" points="22,46 26,57 37,57 28,64 31,75 22,68.5 13,75 16,64 7,57 18,57"/>
      <polygon class="icon-line" transform="translate(106 0)" points="22,46 26,57 37,57 28,64 31,75 22,68.5 13,75 16,64 7,57 18,57"/>
    </svg>
    <h2 class="feature-title" style="margin-top:56px;">Professional<br>Service</h2>
    <p class="feature-text" style="margin-top:8px; width:222px;">When you hire a Varno Electrical Electrician you will get a professional and well-presented Electrician that comes skilled and ready to do the job.</p>
  </section>

  <section class="feature" style="left:298px; top:522px; width:230px;">
    <svg class="feature-icon" width="84" height="124" viewBox="0 0 100 120">
      <polygon class="icon-line" points="50,12 58,20.6 69.8,20.2 69.4,32 78,40 69.4,48 69.8,59.8 58,59.4 50,68 42,59.4 30.2,59.8 30.6,48 22,40 30.6,32 30.2,20.2 42,20.6"/>
      <circle class="icon-line" cx="50" cy="40" r="15"/>
      <polyline class="icon-line" points="38,62 22,103 35,98 42,112 50,86"/>
      <polyline class="icon-line" points="62,62 82,112 68,104 62,114 50,86"/>
    </svg>
    <h2 class="feature-title" style="margin-top:36px;">5 year workmanship<br>guarantee</h2>
    <p class="feature-text" style="margin-top:8px; width:222px;">You can buy with confidence as all of our work has a 5 year workmanship guarantee. For your peace of mind, we unconditionally back our electrical work. We will come back to fix any problems at our own expense.</p>
  </section>

  <section class="feature" style="left:543px; top:510px; width:230px;">
    <svg class="feature-icon" width="150" height="150" viewBox="0 0 150 150">
      <circle class="icon-line" cx="75" cy="75" r="73"/>
      <circle class="icon-line" cx="75" cy="75" r="67"/>
      <path class="icon-line" d="M96,46 C90,38 82,34 74,34 C60,34 53,42 53,52 C53,64 64,68 75,72 C88,76 97,80 97,94 C97,106 88,114 75,114 C64,114 55,109 49,100 M75,22 V34 M75,114 V128"/>
    </svg>
    <h2 class="feature-title" style="margin-top:20px;">Value for<br>money</h2>
    <p class="feature-text" style="margin-top:8px; width:222px;">We provide extremely competitive pricing, which means you get value for money on quality that is comparable to the best in the industry.</p>
  </section>

  <!-- Row two -->
  <section class="feature" style="left:175px; top:882px; width:230px;">
    <svg class="feature-icon" width="140" height="100" viewBox="0 0 140 100">
      <path class="icon-line" d="M28,2 C12,18 18,50 54,62 C54,38 48,20 28,2 Z M30,16 L52,58"/>
      <path class="icon-line" d="M104,2 C84,10 74,34 80,52 C98,44 106,26 104,2 Z M100,14 L82,48"/>
      <path class="icon-line" d="M138,34 C110,32 76,52 70,82 C70,96 100,98 118,84 C132,72 138,52 138,34 Z M128,48 L68,94"/>
      <path class="icon-line" d="M2,72 C20,56 48,60 62,72 C44,88 18,92 2,72 Z M10,72 L60,72"/>
    </svg>
    <h2 class="feature-title" style="margin-top:44px;">Environmentally<br>friendly</h2>
    <p class="feature-text" style="margin-top:8px; width:222px;">We a committed to reducing carbon emissions by installing Solar Power and upgrading sites to LED Lighting. In addition to reducing the carbon emissions we recycle Fluorescent Tubes, Highbay Globes, Metal and Cardboard.</p>
  </section>

  <section class="feature" style="left:415px; top:890px; width:230px;">
    <svg class="feature-icon" width="104" height="106" viewBox="0 0 104 106">
      <path class="icon-line" d="M2,4 C20,14 36,12 52,2 C68,12 84,14 102,4 V66 C102,76 94,84 52,104 C10,84 2,76 2,66 Z"/>
    </svg>
    <h2 class="feature-title" style="margin-top:34px;">Fully<br>insured</h2>
    <p class="feature-text" style="margin-top:8px; width:230px;">Varno Electrical is fully insured and equipped to handle break downs and service call outs.</p>
  </section>
</div>
</body>
</html>
```